Wholesale in Gold Jewellery & Gold Bullion

We are an established gold jewellery and gold bullion wholesaler selling these products to international clients. We already have a name and logo of our company, hence please view attached current card design. We need a completely new design to compliment our business and industry and the final design should be new and elegant.

Contact Information for Business Card

New card details must be same as per current card. Like logo, name, tel no. & etc.

Colors

Designer to choose colors to be used in the design.

```html
<!DOCTYPE html>
<html lang="en">
<head>
<meta charset="utf-8">
<title>Arjun &amp; Co – Business Card</title>
<link rel="stylesheet" href="https://fonts.googleapis.com/css2?family=Bebas+Neue&family=Open+Sans:wght@400&display=swap">
<style>
  :root {
    --stage: #2b2b2b;
    --paper: #eeeeee;
    --gold: #d9960f;
    --ink: #222222;
    --rule: #b8b8b8;
    --white: #ffffff;
  }
  * { margin: 0; padding: 0; box-sizing: border-box; }
  html, body { width: 1200px; height: 1200px; overflow: hidden; }
  body { background: var(--stage); position: relative; font-family: "Open Sans", sans-serif; }

  .card { position: absolute; top: 310px; width: 366px; height: 594px; overflow: hidden; }
  .card--front { left: 233px; background: var(--paper); }
  .card--back { left: 628px; width: 368px; background: var(--gold); }

  .brand-mark { position: absolute; top: 80px; left: 0; width: 100%; text-align: center; }
  .brand-mark__dot { display: block; width: 96px; height: 96px; margin: 0 auto 14px; border-radius: 50%; background: var(--gold); }
  .brand-mark__name { font-family: "Bebas Neue", sans-serif; font-size: 40px; color: var(--gold); letter-spacing: 1px; line-height: 1; }

  .person { position: absolute; top: 372px; width: 100%; text-align: center; }
  .person__name { font-family: "Bebas Neue", sans-serif; font-weight: 400; font-size: 40px; color: var(--gold); line-height: 1; letter-spacing: 0.3px; }
  .person__role { font-size: 17px; line-height: 22px; color: var(--ink); margin-top: 1px; }

  .contact-icons { position: absolute; top: 440px; left: 0; width: 100%; display: flex; justify-content: center; align-items: center; gap: 4px; }
  .contact-icons__rule { width: 48px; height: 1px; background: var(--rule); margin: 0 6px; }
  .contact-icons svg { width: 24px; height: 24px; }

  .contact-list { position: absolute; top: 471px; width: 100%; text-align: center; font-size: 17px; line-height: 21.5px; color: var(--ink); list-style: none; }

  .company { position: absolute; top: 434px; width: 100%; text-align: center; font-family: "Bebas Neue", sans-serif; font-weight: 400; font-size: 64px; line-height: 1; color: var(--white); letter-spacing: 0.5px; }
  .address { position: absolute; top: 512px; width: 100%; text-align: center; font-size: 17px; line-height: 21px; color: var(--white); font-style: normal; }
</style>
</head>
<body>
  <section class="card card--front" aria-label="Card front">
    <div class="brand-mark">
      <span class="brand-mark__dot"></span>
      <span class="brand-mark__name">Arjun &amp; Co</span>
    </div>

    <div class="person">
      <h1 class="person__name">Dinesh Varadan</h1>
      <p class="person__role">Director</p>
    </div>

    <div class="contact-icons" aria-hidden="true">
      <span class="contact-icons__rule"></span>
      <svg viewBox="0 0 24 24"><circle cx="12" cy="12" r="11" fill="none" stroke="#d9960f" stroke-width="2"/><path d="M6 10c0-2 3-3 6-3s6 1 6 3l-2 1-1-2H9l-1 2zM8 12h8l1 5H7z" fill="#d9960f"/></svg>
      <svg viewBox="0 0 24 24"><circle cx="12" cy="12" r="11" fill="none" stroke="#d9960f" stroke-width="2"/><rect x="8.5" y="5.5" width="7" height="13" rx="1.5" fill="none" stroke="#d9960f" stroke-width="1.6"/></svg>
      <svg viewBox="0 0 24 24"><circle cx="12" cy="12" r="11" fill="none" stroke="#d9960f" stroke-width="2"/><rect x="8" y="5.5" width="8" height="4" fill="#d9960f"/><rect x="6" y="10" width="12" height="5" rx="1" fill="#d9960f"/><rect x="8" y="15.5" width="8" height="3" fill="none" stroke="#d9960f" stroke-width="1.4"/></svg>
      <svg viewBox="0 0 24 24"><circle cx="12" cy="12" r="11" fill="none" stroke="#d9960f" stroke-width="2"/><rect x="6" y="8" width="12" height="8" fill="none" stroke="#d9960f" stroke-width="1.6"/><path d="M6 8l6 5 6-5" fill="none" stroke="#d9960f" stroke-width="1.6"/></svg>
      <span class="contact-icons__rule"></span>
    </div>

    <ul class="contact-list">
      <li>+65 6100 2400</li>
      <li>+65 9100 4521</li>
      <li>+65 6100 2499</li>
      <li>dinesh@arjunco.com</li>
    </ul>
  </section>

  <section class="card card--back" aria-label="Card back">
    <h2 class="company">Arjun &amp; Co</h2>
    <address class="address">12 Lower Ridge Rd,<br>Singapore 100482</address>
  </section>
</body>
</html>
```